Business Card Design

We have recently seen two business cards that caught our attention and think the designs would work for us. We are an accounting firm that serves small businesses in a variety of industries. Attached are the two business card that inspired us along with very rough layouts. We would like to see a professional layout using our company information.

Industry/Entity Type

Accounting

Contact Information for Business Card

Company Name - Marlowe Thistle
Address - 4182 Orlanby Lane, Suite 610, Houston, TX 77093
713-555-0187 - Main
281-555-0342 - Fax

Team Member Names, emails and phone numbers (see attachment)

```html
<!DOCTYPE html>
<html lang="en">
<head>
<meta charset="utf-8">
<title>Marlowe Thistle – Business Card</title>
<link href="https://fonts.googleapis.com/css2?family=Exo+2:wght@400;600&display=swap" rel="stylesheet">
<style>
  :root {
    --backdrop: #cdc8c3;
    --charcoal: #353535;
    --slate: #8b8b8b;
    --pill: #7d7d7d;
    --paper: #f4f4f4;
    --silver: #c9c9c9;
    --ink: #3a3a3a;
    --light-text: #f2f2f2;
    --shadow: rgba(0, 0, 0, 0.22);
  }
  * { margin: 0; padding: 0; box-sizing: border-box; }
  html, body {
    width: 1200px; height: 802px; overflow: hidden;
    background: var(--backdrop);
    font-family: "Exo 2", sans-serif;
  }
  .canvas { position: relative; width: 1200px; height: 802px; }
  .card {
    position: absolute; top: 246px;
    width: 540px; height: 309px;
    box-shadow: 0 10px 28px var(--shadow);
    overflow: hidden;
  }
  .card--front { left: 40px; }
  .card--back { left: 620px; }
  .card__art { position: absolute; inset: 0; width: 100%; height: 100%; }
  .card__text { position: absolute; white-space: nowrap; }

  .brand {
    left: 112px; top: 74px;
    display: flex; align-items: center; gap: 12px;
    font-size: 30px; font-weight: 600; color: var(--ink);
  }
  .brand__mark { width: 22px; height: 22px; background: var(--ink); }

  .contact {
    display: flex; align-items: flex-start; gap: 10px;
    color: var(--light-text); font-size: 12px; letter-spacing: 0.6px; line-height: 1.45;
  }
  .contact__icon { flex: none; width: 18px; display: flex; justify-content: center; margin-top: 2px; }
  .contact--phone { left: 22px; top: 148px; }
  .contact--address { left: 22px; top: 194px; }
  .contact--email { left: 206px; top: 266px; font-size: 15px; align-items: center; letter-spacing: 0.8px; }
  .contact--email .contact__icon { width: 24px; margin-top: 0; }

  .web--front { left: 240px; top: 183px; color: var(--light-text); font-size: 15px; letter-spacing: 0.8px; }

  .person { left: 30px; top: 28px; color: var(--light-text); }
  .person__name { font-size: 20px; letter-spacing: 2px; font-weight: 400; }
  .person__title { font-size: 12px; letter-spacing: 1px; margin-top: 2px; color: var(--silver); }
  .web--back { right: 30px; top: 130px; color: var(--light-text); font-size: 16px; letter-spacing: 1px; }
</style>
</head>
<body>
<main class="canvas">

  <section class="card card--front" aria-label="Card front">
    <svg class="card__art" viewBox="0 0 540 309" aria-hidden="true">
      <defs>
        <linearGradient id="paperSheen" x1="0" y1="0" x2="1" y2="1">
          <stop offset="0" stop-color="#ffffff"/>
          <stop offset="1" stop-color="#dedede"/>
        </linearGradient>
      </defs>
      <rect width="540" height="309" fill="var(--charcoal)"/>
      <rect width="540" height="60" fill="var(--slate)"/>
      <path d="M0 52 H540 V242 H250 Q228 242 222 222 L214 150 Q210 134 190 134 H0 Z" fill="url(#paperSheen)"/>
      <line x1="0" y1="52" x2="540" y2="52" stroke="var(--silver)" stroke-width="4"/>
      <rect x="222" y="166" width="290" height="50" rx="16" fill="var(--pill)"/>
    </svg>

    <div class="card__text brand">
      <span class="brand__mark"></span>
      <span>Marlowe Thistle</span>
    </div>

    <div class="card__text contact contact--phone">
      <span class="contact__icon"><svg width="14" height="16" viewBox="0 0 14 16"><path d="M3 1 L6 1 L6 5 L4 6 Q5 10 8 11 L9 9 L13 10 L13 13 Q12 15 9 15 Q2 13 1 4 Q1 1 3 1 Z" fill="var(--light-text)"/></svg></span>
      <div>713-555-0187<br>281-555-0342</div>
    </div>

    <div class="card__text contact contact--address">
      <span class="contact__icon"><svg width="18" height="16" viewBox="0 0 18 16"><path d="M9 1 L17 8 H14 V15 H11 V10 H7 V15 H4 V8 H1 Z" fill="var(--light-text)"/></svg></span>
      <div>4182 Orlanby Lane,<br>Suite 610,<br>Houston, TX 77093</div>
    </div>

    <div class="card__text web--front">www.marlowethistle.com</div>

    <div class="card__text contact contact--email">
      <span class="contact__icon"><svg width="24" height="16" viewBox="0 0 24 16"><rect x="1" y="1" width="22" height="14" fill="none" stroke="var(--light-text)" stroke-width="1.5"/><path d="M1 1 L12 9 L23 1" fill="none" stroke="var(--light-text)" stroke-width="1.5"/></svg></span>
      <span>office@marlowethistle.com</span>
    </div>
  </section>

  <section class="card card--back" aria-label="Card back">
    <svg class="card__art" viewBox="0 0 540 309" aria-hidden="true">
      <rect width="540" height="309" fill="var(--charcoal)"/>
      <path d="M0 200 H200 Q222 200 228 220 L236 250 Q242 270 262 270 H400 V309 H0 Z" fill="var(--slate)"/>
      <path d="M0 214 H188 Q206 214 212 230 L220 256 Q226 282 250 282 H0 Z" fill="var(--paper)"/>
      <path d="M200 200 Q222 200 228 220 L236 250 Q242 270 262 270 H400" fill="none" stroke="var(--silver)" stroke-width="3"/>
    </svg>

    <div class="card__text person">
      <div class="person__name">TEODOR VANCE</div>
      <div class="person__title">Managing Director</div>
    </div>
    <div class="card__text web--back">www.marlowethistle.com</div>
  </section>

</main>
</body>
</html>
```